Bright bears day nursery qrp limited

we would like create a website that can be updated by us easily as we have regular changes to what we provide and need. we would like something that is classy but also appealing from a child's aspect. we would be looking to add our own logo and our kinderwatch logo both attached, if you guys can create it and we will work with the preferred choice to add all the text.
We would like the links to family pathways, kinderwatch report and our chatterbook feed on the front page

we are looking for a website for our childcare business we have 2 nurseries that we would like one website.
showing our opening hours, price list, policies etc as well as photos, description of our day, staff photos and their training accreditation's.

Target Market(s)

Families

Industry/Entity Type

Childcare

Number of Pages Required

5+ page

Font styles to use
Serif

Colors

Designer to choose colors to be used in the design.

Requirements
Must have
• links to social media and other websites, photographs, links to download registration forms etc, parents able to leave reviews. google maps link, job opportunities
Nice to have
• facilities to take payments

```html
<!DOCTYPE html>
<html lang="en">
<head>
<meta charset="utf-8">
<title>Bright Bears Day Nursery QRP Limited</title>
<link rel="stylesheet" href="https://fonts.googleapis.com/css2?family=Open+Sans:wght@400;600;700;800&family=Raleway:wght@600;700;800&display=swap">
<style>
:root{
  --navy:#1f2e5a;
  --navy-dark:#16213f;
  --footer:#1c2645;
  --footer-bottom:#121a31;
  --green:#4aa83f;
  --green-dark:#3a8c31;
  --magenta:#d6187f;
  --red:#d3263a;
  --text:#444;
  --muted:#777;
  --line:#d9dde5;
  --white:#fff;
  --light:#f4f5f8;
}
*{box-sizing:border-box;margin:0;padding:0}
html,body{width:1200px;height:3272px;overflow:hidden}
body{font-family:"Open Sans",Arial,sans-serif;color:var(--text);background:var(--white);font-size:13px;line-height:1.6}
.wrap{width:1056px;margin:0 auto;position:relative}
h2.section-title{font-family:"Raleway","Open Sans",sans-serif;font-weight:800;font-size:26px;color:#222;text-transform:uppercase;text-align:center;letter-spacing:.5px}
.btn{display:inline-block;background:var(--navy);color:var(--white);font-weight:700;font-size:12px;padding:10px 22px;letter-spacing:.5px;text-transform:uppercase}

/* header */
.site-header{height:144px}
.site-header .wrap{height:144px;display:flex;justify-content:space-between;align-items:center}
.brand{display:flex;align-items:center;gap:14px;font-family:"Raleway",sans-serif;font-weight:800;color:var(--navy);font-size:22px;line-height:1.1;text-transform:uppercase}
.brand-mark{width:70px;height:70px;border-radius:50%;background:var(--green)}
.opening-hours{width:290px;font-size:14px}
.opening-hours h4{color:var(--red);font-weight:800;font-size:15px;text-transform:uppercase}
.opening-hours dl{display:grid;grid-template-columns:1fr auto;row-gap:2px}
.opening-hours dt{color:#333}
.opening-hours dd{color:var(--magenta)}

/* nav */
.main-nav{height:40px;background:var(--navy)}
.main-nav ul{list-style:none;display:flex;height:40px}
.main-nav li{color:var(--white);font-weight:700;font-size:12.5px;padding:0 19px;line-height:40px;text-transform:uppercase}
.main-nav li.active{background:var(--green)}

/* hero */
.hero{height:476px;background:linear-gradient(120deg,#1c5b8e 0%,#c79a6b 35%,#e5c9a8 55%,#b8d0e8 75%,#d94f6a 100%)}

/* welcome */
.welcome{height:330px;padding-top:44px}
.welcome .wrap{display:flex;justify-content:space-between}
.welcome-text{width:720px}
.welcome-text h2{font-family:"Raleway",sans-serif;font-weight:800;font-size:26px;color:#222;text-transform:uppercase;margin-bottom:12px}
.welcome-text p{font-size:13px;color:var(--muted);margin-bottom:22px;line-height:1.75}
.day-box{width:240px;height:236px;background:var(--green);color:var(--white);padding:22px 20px;text-align:center}
.day-box h3{font-family:"Raleway",sans-serif;font-weight:800;font-size:22px;line-height:1.2;text-transform:uppercase;margin-bottom:14px}
.day-box p{font-size:11.5px;font-style:italic;line-height:1.6}

/* pricing */
.pricing{height:830px;position:relative;overflow:hidden}
.pricing-bg{position:absolute;inset:0;background:linear-gradient(135deg,#3b3a2e 0%,#2a3024 40%,#1d2624 70%,#3a2f2a 100%)}
.pricing-shade{position:absolute;inset:0;background:rgba(10,14,20,.55)}
.pricing .wrap{padding-top:48px;z-index:1}
.pricing h2.section-title{color:var(--white);margin-bottom:40px;border-bottom:1px solid rgba(255,255,255,.35);padding-bottom:14px;width:420px;margin-left:auto;margin-right:auto}
.price-table{width:860px;margin:0 auto;border-collapse:collapse;background:var(--white)}
.price-table th{height:48px;color:var(--white);font-size:17px;font-weight:600}
.price-table th.blank{background:transparent}
.price-table th.under2{background:var(--navy)}
.price-table th.over2{background:var(--magenta)}
.price-table td{border:1px solid var(--line);height:64px;text-align:center;font-size:15px;color:#333}
.price-table td.label{text-align:left;padding-left:14px;width:220px;font-family:"Raleway",sans-serif;font-weight:800;font-size:18px;color:#222;line-height:1.15}
.price-table td.label small{display:block;font-family:"Open Sans",sans-serif;font-weight:600;font-size:11px;color:var(--magenta)}
.price-table td small.note{display:block;font-size:10.5px;color:var(--green)}
.pricing-notes{margin-top:36px;text-align:center;color:var(--white);font-size:13px;line-height:1.75}
.pricing-notes .highlight{color:var(--green);font-weight:700;text-transform:uppercase}
.pricing-notes p{margin-bottom:8px}

/* staff */
.staff{height:490px;padding-top:46px}
.staff h2.section-title{margin-bottom:30px}
.staff-grid{display:flex;justify-content:space-between}
.staff-card{width:240px;border:1px solid var(--line);text-align:center}
.staff-photo{height:230px;background:linear-gradient(160deg,#d9b99a,#8e7560)}
.staff-card:nth-child(2) .staff-photo{background:linear-gradient(160deg,#f0d4b8,#a06d54)}
.staff-card:nth-child(3) .staff-photo{background:linear-gradient(160deg,#c9a06e,#6e4a32)}
.staff-card:nth-child(4) .staff-photo{background:linear-gradient(160deg,#e9d2b6,#b08a67)}
.staff-card h4{font-family:"Raleway",sans-serif;font-weight:800;font-size:13px;color:#222;margin:14px 0 4px;text-transform:uppercase}
.staff-card p{font-size:11px;color:var(--muted);padding:0 16px;line-height:1.55}
.social-dots{display:flex;justify-content:center;gap:10px;padding:10px 0 12px}
.social-dots span{width:12px;height:12px;border-radius:50%;background:#9aa3b5}

/* training + gallery */
.training-gallery{height:360px;background:var(--light);padding-top:34px}
.training-gallery .wrap{display:flex;justify-content:space-between}
.training{width:590px}
.training h2,.gallery h2{font-family:"Raleway",sans-serif;font-weight:800;font-size:26px;color:#222;text-transform:uppercase;margin-bottom:16px}
.training-body{display:flex;gap:22px}
.training-photo{width:210px;height:210px;flex:none;background:linear-gradient(150deg,#cdb89c,#7c6a58)}
.training-body p{font-size:12.5px;color:var(--muted);margin-bottom:18px;line-height:1.7}
.gallery{width:430px}
.gallery-grid{display:grid;grid-template-columns:repeat(3,136px);grid-auto-rows:82px;gap:11px}
.gallery-grid div:nth-child(3n+1){background:linear-gradient(140deg,#c35d4a,#e8c06a)}
.gallery-grid div:nth-child(3n+2){background:linear-gradient(140deg,#6fa2c9,#e2d2b3)}
.gallery-grid div:nth-child(3n){background:linear-gradient(140deg,#8fb85c,#d9784f)}

/* feed */
.feed{height:290px;padding-top:40px}
.feed h2.section-title{margin-bottom:36px}
.feed-grid{display:flex;justify-content:space-between}
.feed-post{width:320px;display:flex;gap:14px}
.feed-avatar{width:56px;height:56px;border-radius:50%;background:var(--green);flex:none}
.feed-post h5{font-size:12.5px;font-weight:700;color:var(--navy)}
.feed-post p{font-size:11.5px;color:var(--muted);line-height:1.55}

/* footer */
.site-footer{height:272px;background:var(--footer);color:#c8cede;padding-top:34px}
.site-footer .wrap{display:flex;gap:40px}
.footer-col h5{color:var(--white);font-weight:800;font-size:13px;text-transform:uppercase;margin-bottom:10px}
.footer-col ul{list-style:none;font-size:12px;line-height:1.9}
.sitemap ul{columns:2;column-gap:40px;width:190px}
.contact{width:200px}
.signup{width:200px}
.signup .field{display:flex;margin-top:4px}
.signup .field span{flex:1;background:var(--white);color:#999;font-size:11px;padding:8px}
.signup .field b{background:var(--green);color:var(--white);font-size:11px;padding:8px 10px}
.partners{display:flex;align-items:center;gap:14px;margin-left:auto;margin-top:40px}
.partner-name{font-family:"Raleway",sans-serif;font-weight:800;font-size:20px;color:var(--white);line-height:1.05}
.partner-badge{width:78px;height:78px;background:#2f4b8f}
.footer-bottom{height:40px;background:var(--footer-bottom);color:#8b93a8;font-size:11px}
.footer-bottom .wrap{display:flex;justify-content:space-between;align-items:center;height:40px}
.footer-bottom .social-dots{padding:0}
.footer-bottom .social-dots span{background:#8b93a8}
</style>
</head>
<body>

<header class="site-header">
  <div class="wrap">
    <div class="brand"><span class="brand-mark"></span><span>Bright Bears<br>Day Nursery</span></div>
    <div class="opening-hours">
      <h4>Opening Hours:</h4>
      <dl>
        <dt>Monday - Friday</dt><dd>7:30 am - 6:00 pm</dd>
        <dt>Saturday</dt><dd>8:00 am - 1:00 pm</dd>
        <dt>Sunday</dt><dd>Closed</dd>
      </dl>
    </div>
  </div>
</header>

<nav class="main-nav">
  <div class="wrap">
    <ul>
      <li class="active">Home</li><li>About Us</li><li>Services</li><li>Pricing</li><li>Staff</li><li>Gallery</li><li>Blog</li><li>News &amp; Events</li><li>Contact Us</li>
    </ul>
  </div>
</nav>

<section class="hero" role="img" aria-label="Photo of young children playing together in a bright nursery classroom"></section>

<section class="welcome">
  <div class="wrap">
    <div class="welcome-text">
      <h2>Welcome to our website</h2>
      <p>Every day at our nurseries is filled with play, discovery and care. Our friendly team creates a warm, safe space where little ones can grow in confidence, make friends and learn through hands-on activities. We work closely with families to support each child at their own pace, from their very first settling-in visit to the day they head off to school. Come and see what makes our rooms feel like home.</p>
      <span class="btn">Read More</span>
    </div>
    <aside class="day-box">
      <h3>Description of our day</h3>
      <p>"Our days begin with a warm breakfast and free play, followed by group time, outdoor fun, a hot lunch, quiet rest and creative afternoon activities."</p>
    </aside>
  </div>
</section>

<section class="pricing">
  <div class="pricing-bg" role="img" aria-label="Photo of a nursery playroom with toys, dimmed behind the price list"></div>
  <div class="pricing-shade"></div>
  <div class="wrap">
    <h2 class="section-title">Our Pricing</h2>
    <table class="price-table">
      <tr><th class="blank"></th><th class="under2">Under 2's</th><th class="over2">2-5's</th></tr>
      <tr><td class="label">Half day<small>8am-1pm or 1pm-6pm</small></td><td>£26</td><td>£25</td></tr>
      <tr><td class="label">Full day<small>7:30-6pm</small></td><td>£40</td><td>£38</td></tr>
      <tr><td class="label">Full time<small>Mon - Fri&nbsp;&nbsp;7:30-6pm</small></td><td>£188</td><td>£181<small class="note">Funded children in holidays</small></td></tr>
      <tr><td class="label">Full time funded children<small>3+ years old</small></td><td></td><td>£130<small class="note">During term time</small></td></tr>
    </table>
    <div class="pricing-notes">
      <p>Fees include breakfast, fruit, tea, hot lunch, afternoon snack, nappies and wipes.<br>Extra meals can be offered for an additional charge of £2.50 per meal, per day.</p>
      <p>Please see a member of staff.</p>
      <p class="highlight">Is your child entitled to funding?</p>
      <p>Do you meet the 2 year funding criteria?<br>To apply please take an application form from the nursery or apply online today.<br>3 and 4 year olds are entitled to 15 hours free government funding from the term after their 3rd birthday.<br>Please visit the government website for 30 hours free childcare from September.</p>
      <p class="highlight" style="text-transform:none">https://www.familypathways.example/</p>
    </div>
  </div>
</section>

<section class="staff">
  <div class="wrap">
    <h2 class="section-title">Our Staff</h2>
    <div class="staff-grid">
      <article class="staff-card"><div class="staff-photo" role="img" aria-label="Staff member portrait"></div><h4>Name Heading</h4><p>Caring early years practitioner with a love of stories, songs and outdoor play.</p><div class="social-dots"><span></span><span></span></div></article>
      <article class="staff-card"><div class="staff-photo" role="img" aria-label="Staff member portrait"></div><h4>Name Heading</h4><p>Caring early years practitioner with a love of stories, songs and outdoor play.</p><div class="social-dots"><span></span><span></span></div></article>
      <article class="staff-card"><div class="staff-photo" role="img" aria-label="Staff member portrait with a child"></div><h4>Name Heading</h4><p>Caring early years practitioner with a love of stories, songs and outdoor play.</p><div class="social-dots"><span></span><span></span></div></article>
      <article class="staff-card"><div class="staff-photo" role="img" aria-label="Staff member portrait"></div><h4>Name Heading</h4><p>Caring early years practitioner with a love of stories, songs and outdoor play.</p><div class="social-dots"><span></span><span></span></div></article>
    </div>
  </div>
</section>

<section class="training-gallery">
  <div class="wrap">
    <div class="training">
      <h2>Training Accreditation's</h2>
      <div class="training-body">
        <div class="training-photo" role="img" aria-label="Photo of a nursery room prepared for a training session"></div>
        <div>
          <p>All of our staff hold recognised childcare qualifications and take part in regular training, including first aid, safeguarding, food hygiene and early language support, so your child is always in skilled hands.</p>
          <span class="btn">Read More</span>
        </div>
      </div>
    </div>
    <div class="gallery">
      <h2>Photo Gallery</h2>
      <div class="gallery-grid" role="img" aria-label="Grid of nursery activity photos">
        <div></div><div></div><div></div><div></div><div></div><div></div><div></div><div></div><div></div>
      </div>
    </div>
  </div>
</section>

<section class="feed">
  <div class="wrap">
    <h2 class="section-title">Chatterbook Feed</h2>
    <div class="feed-grid">
      <article class="feed-post"><span class="feed-avatar"></span><div><h5>Bright Bears Day Nursery QRP</h5><p>What a fantastic way to celebrate being open a year! Thank you to every family who joined our party today.</p></div></article>
      <article class="feed-post"><span class="feed-avatar"></span><div><h5>Bright Bears Day Nursery QRP</h5><p>What a fantastic way to celebrate being open a year! Thank you to every family who joined our party today.</p></div></article>
      <article class="feed-post"><span class="feed-avatar"></span><div><h5>Bright Bears Day Nursery QRP</h5><p>What a fantastic way to celebrate being open a year! Thank you to every family who joined our party today.</p></div></article>
    </div>
  </div>
</section>

<footer>
  <div class="site-footer">
    <div class="wrap">
      <div class="footer-col sitemap">
        <h5>Site Map</h5>
        <ul><li>Home</li><li>About Us</li><li>Services</li><li>Pricing</li><li>Staff</li><li>Gallery</li><li>Blog</li><li>News &amp; Events</li><li>Contact</li></ul>
      </div>
      <div class="footer-col contact">
        <h5>Contact Info</h5>
        <ul><li>12 Maple Row</li><li>Brookfield BF4 7QD</li><li>01632 960 418</li><li>hello@brightbears.example</li><li>Location Map</li></ul>
      </div>
      <div class="footer-col signup">
        <h5>Email Sign Up</h5>
        <div class="field"><span>Email Address</span><b>SIGN UP</b></div>
      </div>
      <div class="partners">
        <span class="partner-name">Family<br>Pathways</span>
        <span class="partner-badge"></span>
        <span class="partner-badge"></span>
      </div>
    </div>
  </div>
  <div class="footer-bottom">
    <div class="wrap">
      <span>Copyright © 2017 Company Name. All Rights Reserved. | Policies</span>
      <div class="social-dots"><span></span><span></span><span></span><span></span></div>
    </div>
  </div>
</footer>

</body>
</html>
```